One piece Trade show banner, 8' x 8' square

One piece banner for trade show
8' x 8' airborne geophysical company

Target Market(s)

Business

Industry/Entity Type

mineral exploration and science

Colors
0054AA
0677BA
7BADD7
CADEEF
E8F1F8
FFC000
F8CF3A
FAE287
FDF2CF
FEFAEE

Requirements
Must have
• Company logo (attached), slogan (Airborne Geophysics for Discovery). We are looking for a new banner, for a standard 8 x 8' square one-piece booth. I have attached some pictures, our logo, our old banner for reference, and two examples from unrelated companies from a tradeshow that we like. If its possible I'd like to change the color of the helicopter from green to dark grey. IE, keep the orange and white, just change green to dark grey. Looking for a simple, clean design with minimal text.
Nice to have
• I have attached examples of banners that we like (2xIMG), plus our old 3-piece banner r.
Should not have
• Green in the helicopter. Please change the color of the helicopter with green/orange/white to dark grey/orange/white. IE change the green to dark grey and leave the orange and white alone. I've attached lots of pictures but I don't expect them all to be used.

```html
<!DOCTYPE html>
<html lang="en">
<head>
<meta charset="utf-8">
<title>Northline Aerial – Airborne Geophysics for Discovery</title>
<link href="https://fonts.googleapis.com/css2?family=Jost:ital,wght@0,400;0,500;0,700;1,800&display=swap" rel="stylesheet">
<style>
  :root {
    --blue-deep: #0054AA;
    --blue-mid: #0677BA;
    --blue-soft: #7BADD7;
    --blue-pale: #CADEEF;
    --bg: #E2EDF7;
    --gold: #FFC000;
    --ink: #111111;
    --white: #FFFFFF;
  }
  * { margin: 0; padding: 0; box-sizing: border-box; }
  html, body { width: 1200px; height: 1200px; overflow: hidden; }
  body { background: var(--bg); font-family: "Jost", "Futura", sans-serif; }
  .banner { position: relative; width: 1200px; height: 1200px; overflow: hidden; background: var(--bg); }

  .scenery { position: absolute; inset: 0; width: 1200px; height: 1200px; }

  .frame {
    position: absolute; left: 45px; top: 45px; width: 1110px; height: 1110px;
    border: 3px solid var(--blue-soft); border-radius: 38px; pointer-events: none;
  }

  .headline {
    position: absolute; left: 92px; top: 92px;
    color: var(--blue-deep); font-style: italic; font-weight: 800; line-height: 1;
  }
  .headline-top { display: block; font-size: 46px; letter-spacing: 0.5px; }
  .headline-bottom { display: block; margin-top: 4px; white-space: nowrap; }
  .headline-for { font-size: 28px; font-weight: 500; font-style: normal; margin-right: 12px; }
  .headline-key { font-size: 84px; letter-spacing: 1px; }
  .headline-rule {
    display: block; width: 120px; height: 8px; margin-top: 18px;
    background: var(--gold); border-radius: 4px;
  }

  .brand {
    position: absolute; right: 102px; top: 100px;
    color: var(--ink); font-size: 40px; font-weight: 500; line-height: 1; letter-spacing: 0.5px;
  }

  .service { position: absolute; width: 420px; }
  .service h2 { font-size: 30px; font-weight: 700; color: var(--ink); line-height: 38px; letter-spacing: 0.2px; }
  .service ul { list-style: none; }
  .service li {
    position: relative; padding-left: 28px;
    font-size: 31px; font-weight: 400; color: var(--blue-deep); line-height: 38px; letter-spacing: 0.3px;
  }
  .service li::before {
    content: ""; position: absolute; left: 5px; top: 16px;
    width: 8px; height: 8px; border-radius: 50%; background: var(--blue-deep);
  }
  .svc-em { left: 193px; top: 315px; }
  .svc-mag { left: 728px; top: 315px; }
  .svc-rad { left: 193px; top: 504px; }
  .svc-con { left: 728px; top: 504px; }

  .web {
    position: absolute; left: 689px; top: 1138px; width: 407px; height: 34px;
    background: var(--white); border-radius: 17px;
    color: var(--blue-deep); font-size: 23px; font-weight: 400; line-height: 34px; text-align: center; letter-spacing: 0.3px;
  }
</style>
</head>
<body>
<main class="banner">
  <svg class="scenery" viewBox="0 0 1200 1200" xmlns="http://www.w3.org/2000/svg">
    <defs>
      <linearGradient id="photoTone" x1="0" y1="0" x2="1" y2="1">
        <stop offset="0" stop-color="#8A7890"/>
        <stop offset="0.5" stop-color="#6A6A92"/>
        <stop offset="1" stop-color="#3F5C98"/>
      </linearGradient>
    </defs>
    <path class="accent-wave" fill="var(--blue-deep)" d="M760,830 C880,790 1060,800 1200,890 L1200,1200 L760,1200 Z"/>
    <path class="photo-area" role="img" aria-label="Photo of a white, orange and dark grey survey helicopter with sensor booms flying in front of a rocky snow-dusted mountain face"
          fill="url(#photoTone)"
          d="M0,805 C120,720 230,665 335,663 C520,660 680,740 790,830 C880,905 960,1000 1020,1080 C1060,1130 1090,1170 1112,1200 L0,1200 Z"/>
  </svg>

  <div class="frame"></div>

  <header class="headline">
    <h1>
      <span class="headline-top">Airborne Geophysics</span>
      <span class="headline-bottom"><span class="headline-for">for</span><span class="headline-key">Discovery</span></span>
    </h1>
    <span class="headline-rule"></span>
  </header>

  <div class="brand">Northline Aerial</div>

  <section class="service svc-em">
    <h2>Electromagnetics</h2>
    <ul><li>Frequency domain</li><li>Time domain</li><li>Passive</li></ul>
  </section>
  <section class="service svc-mag">
    <h2>Magnetics</h2>
    <ul><li>Helicopter, fixed wing,<br>and drone</li><li>Total field and gradient</li></ul>
  </section>
  <section class="service svc-rad">
    <h2>Radiometrics</h2>
    <ul><li>256/512 channels</li><li>Up to 33 litres</li></ul>
  </section>
  <section class="service svc-con">
    <h2>Consulting</h2>
    <ul><li>Survey design</li><li>Interpretations</li><li>Inversions</li></ul>
  </section>

  <div class="web">www.northlineaerial.com</div>
</main>
</body>
</html>
```